Professional Package for CPA Firm

We would like a stationery design for our new CPA Firm based in Atlanta, GA called 'Vale 8'. We work with investors to help grow investments, tax free. We would like the design to have a professional/minimal look with a 'wow' factor. We need 9.5″ x 4.125″, 9x12, and 10x13 mailing envelopes, business cards, and a letterhead. We have a logo that is already complete. For the letterhead, we would like to have space to put credentials at the bottom of the page

Industry/Entity Type

CPA, Accounting

```html
<!DOCTYPE html>
<html lang="en">
<head>
<meta charset="utf-8">
<title>Vale 8 — Business Card</title>
<link href="https://fonts.googleapis.com/css2?family=Open+Sans:wght@400;600&display=swap" rel="stylesheet">
<style>
  :root {
    --page: #e9ebee;
    --navy: #0f3352;
    --coral: #f2585d;
    --teal: #1fb6c4;
    --white: #f4f5f6;
    --silver: #c8ccd1;
    --ink-light: #e6ebf0;
  }
  * { box-sizing: border-box; margin: 0; padding: 0; }
  html, body {
    width: 1200px;
    height: 874px;
    overflow: hidden;
    background: var(--page);
    font-family: "Open Sans", sans-serif;
  }
  .sheet {
    width: 1200px;
    height: 874px;
    display: flex;
    align-items: center;
    justify-content: center;
    gap: 60px;
  }
  .card {
    width: 400px;
    height: 700px;
    background: var(--navy);
    border-radius: 22px;
    position: relative;
    overflow: hidden;
  }

  /* Front */
  .card-front {
    display: flex;
    flex-direction: column;
    align-items: center;
    justify-content: center;
  }
  .brand {
    display: flex;
    align-items: center;
    gap: 14px;
  }
  .brand-dot {
    width: 22px;
    height: 22px;
    border-radius: 50%;
    background: var(--coral);
  }
  .brand-name {
    font-weight: 600;
    font-size: 62px;
    letter-spacing: 2px;
    line-height: 1;
    color: var(--silver);
  }
  .tagline {
    margin-top: 14px;
    font-size: 15px;
    letter-spacing: 2px;
    color: var(--silver);
  }

  /* Back */
  .card-back { padding: 58px 0 0 74px; }
  .person-name {
    font-size: 23px;
    font-weight: 400;
    letter-spacing: 0.5px;
    color: var(--teal);
    text-transform: uppercase;
    line-height: 1.1;
  }
  .person-title {
    font-size: 15px;
    color: var(--coral);
    margin-top: 2px;
  }
  .rule {
    width: 20px;
    height: 1px;
    background: var(--teal);
    margin: 20px 0 14px;
  }
  .address, .contacts {
    font-size: 15px;
    color: var(--ink-light);
    line-height: 1.45;
  }
  .contacts { list-style: none; }
  .contacts li {
    display: flex;
    align-items: center;
    gap: 10px;
  }
  .contacts svg {
    width: 11px;
    height: 11px;
    fill: var(--coral);
    flex: none;
  }
  .mark-area {
    position: absolute;
    left: 34px;
    right: 34px;
    bottom: 40px;
    height: 220px;
    border-radius: 18px;
    background: linear-gradient(90deg, var(--white) 0%, var(--teal) 45%, var(--coral) 100%);
  }
</style>
</head>
<body>
<main class="sheet">
  <section class="card card-front" aria-label="Business card front">
    <div class="brand">
      <span class="brand-dot"></span>
      <span class="brand-name">Vale 8</span>
    </div>
    <p class="tagline">CPAs and Tax Advisors</p>
  </section>

  <section class="card card-back" aria-label="Business card back">
    <h1 class="person-name">Daniel Reyes</h1>
    <p class="person-title">President</p>
    <div class="rule"></div>
    <p class="address">412 Linden Court<br>Atlanta, Georgia 30318</p>
    <div class="rule"></div>
    <ul class="contacts">
      <li>
        <svg viewBox="0 0 12 12" aria-hidden="true"><path d="M2.4 0.8l2 2.2-1 1.4c.7 1.6 2 2.9 3.6 3.6l1.4-1 2.2 2-1.2 2C5 10.8 1.2 7 .8 2z"/></svg>
        404-555-0172
      </li>
      <li>
        <svg viewBox="0 0 12 12" aria-hidden="true"><path d="M3 0h6a1 1 0 0 1 1 1v10a1 1 0 0 1-1 1H3a1 1 0 0 1-1-1V1a1 1 0 0 1 1-1zm.5 1.5v8h5v-8z"/></svg>
        404-555-0193
      </li>
      <li>
        <svg viewBox="0 0 12 12" aria-hidden="true"><path d="M0 2h12v8H0zm1 1v.4l5 3.2 5-3.2V3z"/></svg>
        info@vale8.com
      </li>
      <li>
        <svg viewBox="0 0 12 12" aria-hidden="true"><path d="M6 0a6 6 0 1 0 0 12A6 6 0 0 0 6 0zm0 1.5a4.5 4.5 0 1 1 0 9 4.5 4.5 0 0 1 0-9zM4 5h4v2H4z"/></svg>
        www.vale8.com
      </li>
    </ul>
    <div class="mark-area" role="img" aria-label="Large brand symbol in coral, teal and white"></div>
  </section>
</main>
</body>
</html>
```